Web Design Project for Communications Agency

The design I need (PSD file) is for an agency offering specialised PR and communications services for customers in the healthcare sector.

OBJECTIVES OF THE WEBSITE:
1. To promote the agency's communication services
2. To position Solène Brivard as an industry leader, an expert in healthcare PR and communications by highlighting blogposts and social media.

WHAT I NEED:
1st, I need the design for the Home Page ONLY.
Once approved, I will need the other pages designed as well. (Here is prototype that we've already developed for the Website that will guide you in the design:
http://qorvelle.net/solenebrivard/)

VISUAL INSPIRATION
We want to give this Website a "Flat Design" look. Here are some websites for inspiration :
- http://tavrolinkworks.com/#!/process
- http://www.brindlemoss.co/
- http://quellaroft.com/

Also, reuse images found on the company's current Website :
http://www.solenebrivard.com/fr/index.html

HOMEPAGE MAIN ELEMENTS:
1. Main menu : 6 sections
Accueil | Agence | Services | Approche | Publications | Contact

2. Main Call To Action (big dark rectangle in prototype):
Can be slider or just an information bloc.

3. Publications récentes :
The 4 latest blog posts must be features on the homepage (will be linked with the "Publications" section)

4. Dynamic Footer :
Contains a Twitter feed and a Subscribe to our Newsletter feature (revecez nos publications)

OTHER PAGES (to design once Homepage is approved)
- Agence (about us)
- Services (our team)
- Approche (our approach)
- Publications (blog articles)
- Contact (Contact us)

Industry/Entity Type

Communications

Requirements
Must have
• Please refer to prototype :
http://qorvelle.net/solenebrivard/
Must have ALL features present in prototype.

Also, must reuse this picture in the design : http://solenebrivard.com/static/images/home-big-box.jpg

Finally, you will find attached the company logo.

```html
<!DOCTYPE html>
<html lang="fr">
<head>
<meta charset="utf-8">
<title>Solène Brivard – Communications et affaires publiques</title>
<link href="https://fonts.googleapis.com/css2?family=Ubuntu:wght@300;400;500;700&display=swap" rel="stylesheet">
<style>
  :root {
    --red: #e5404a;
    --ink: #3b3b3b;
    --muted: #6a6a6a;
    --page: #f5f5f5;
    --white: #ffffff;
    --rule: #d9d9d9;
    --bar: #343434;
    --field: #f3f3f3;
    --icon: #8d8d8d;
  }
  * { box-sizing: border-box; margin: 0; padding: 0; }
  html, body { width: 1200px; height: 2285px; overflow: hidden; }
  body {
    position: relative;
    background: var(--page);
    font-family: "Ubuntu", Arial, sans-serif;
    color: var(--ink);
  }

  /* Header */
  .site-header { position: absolute; left: 0; top: 0; width: 1200px; height: 195px; background: var(--white); }
  .brand { position: absolute; left: 130px; top: 62px; display: flex; align-items: center; gap: 12px; }
  .brand-mark { width: 18px; height: 18px; background: var(--red); }
  .brand-name { font-size: 38px; line-height: 44px; font-weight: 400; color: var(--red); white-space: nowrap; }
  .social { position: absolute; left: 870px; top: 20px; display: flex; gap: 5px; }
  .social span { width: 22px; height: 22px; background: var(--icon); border-radius: 3px; display: block; }
  .lang { position: absolute; left: 975px; top: 21px; display: flex; align-items: center; gap: 8px; font-size: 15px; font-weight: 500; color: var(--ink); }
  .lang .flag { width: 24px; height: 15px; background: #3a4f8f; border: 1px solid #ccc; }
  .lang .caret { width: 0; height: 0; border-left: 5px solid transparent; border-right: 5px solid transparent; border-top: 6px solid var(--red); }

  .main-nav { position: absolute; left: 380px; top: 150px; width: 700px; height: 35px; }
  .main-nav a { position: absolute; top: 0; transform: translateX(-50%); font-size: 16px; color: var(--ink); text-decoration: none; white-space: nowrap; }
  .main-nav a.current { color: var(--red); }
  .nav-rule { position: absolute; left: 380px; top: 184px; width: 690px; height: 2px; background: var(--rule); }
  .nav-current-bar { position: absolute; left: 403px; top: 182px; width: 60px; height: 4px; background: var(--red); }
  .search-icon { position: absolute; left: 1048px; top: 156px; }

  /* Hero */
  .hero { position: absolute; left: 0; top: 195px; width: 1200px; height: 450px; }
  .hero-visual {
    position: absolute; inset: 0;
    background:
      radial-gradient(ellipse 260px 300px at 880px 210px, #ffffff 0%, rgba(255,255,255,0) 70%),
      radial-gradient(ellipse 300px 90px at 430px 150px, rgba(229,64,74,.22) 0%, rgba(229,64,74,0) 75%),
      linear-gradient(180deg, #e9e9e9 0%, #f1f1f1 45%, #e3e3e3 100%);
  }
  .hero-title { position: absolute; left: 130px; top: 130px; font-size: 37px; line-height: 50px; font-weight: 300; color: var(--ink); }
  .hero-title u { text-decoration-thickness: 2px; text-underline-offset: 6px; }
  .cta { position: absolute; left: 130px; top: 320px; display: flex; height: 50px; }
  .cta-label { width: 165px; background: var(--red); color: var(--white); font-size: 16px; font-weight: 500; display: flex; align-items: center; justify-content: center; }
  .cta-arrow { width: 50px; background: var(--white); display: flex; align-items: center; justify-content: center; }
  .slider-dots { position: absolute; left: 570px; top: 436px; display: flex; gap: 5px; }
  .slider-dots span { width: 8px; height: 8px; border-radius: 50%; background: #9a9a9a; }
  .slider-dots span.active { background: var(--red); }

  /* Publications */
  .section-bar { position: absolute; left: 130px; top: 688px; width: 40px; height: 4px; background: var(--red); }
  .section-title { position: absolute; left: 130px; top: 692px; font-size: 32px; font-weight: 400; color: var(--ink); }
  .section-rule { position: absolute; left: 130px; top: 738px; width: 940px; height: 1px; background: var(--rule); }

  .post-media { position: absolute; left: 132px; width: 320px; height: 225px; }
  .post-media .photo { width: 100%; height: 100%; }
  .zoom { position: absolute; left: 0; top: 0; width: 0; height: 0; border-top: 40px solid var(--red); border-right: 40px solid transparent; }
  .zoom svg { position: absolute; left: 5px; top: -36px; }
  .thumbs { position: absolute; left: 132px; top: 992px; display: flex; gap: 10px; }
  .thumbs span { width: 72px; height: 46px; display: block; }

  .post-body { position: absolute; left: 510px; width: 560px; }
  .post-body .bar { width: 45px; height: 3px; background: var(--red); }
  .post-title { margin-top: 8px; font-size: 25px; font-weight: 400; color: var(--ink); }
  .post-rule { margin-top: 6px; height: 1px; background: var(--rule); }
  .post-text { margin-top: 10px; font-size: 12.5px; line-height: 17.5px; color: var(--muted); text-align: justify; }
  .post-text + .post-text { margin-top: 18px; }
  .post-btn { margin-top: 14px; width: 110px; height: 35px; background: var(--red); color: var(--white); font-size: 13px; font-weight: 700; display: flex; align-items: center; justify-content: center; }

  /* Footer */
  .site-footer { position: absolute; left: 0; top: 1930px; width: 1200px; height: 303px; background: var(--red); color: var(--white); }
  .footer-heading { position: absolute; top: 40px; font-size: 15px; font-weight: 700; letter-spacing: .3px; }
  .footer-heading::after { content: ""; display: block; margin-top: 6px; width: 300px; height: 1px; background: rgba(255,255,255,.5); }
  .tweets { position: absolute; left: 130px; top: 72px; width: 310px; }
  .tweet { padding: 8px 0 10px; border-bottom: 1px dashed rgba(255,255,255,.6); font-size: 12.5px; line-height: 16px; }
  .tweet:last-child { border-bottom: 0; }
  .tweet em { font-weight: 700; }
  .field { position: absolute; background: var(--field); color: var(--ink); font-size: 11px; padding: 6px 8px; }
  .thanks { position: absolute; left: 642px; top: 245px; font-size: 10px; font-weight: 700; }
  .send { position: absolute; left: 945px; top: 243px; display: flex; height: 37px; }
  .send-label { width: 90px; background: var(--bar); color: var(--white); font-size: 13px; font-weight: 700; display: flex; align-items: center; justify-content: center; }
  .send-icon { width: 33px; background: var(--field); display: flex; align-items: center; justify-content: center; }

  .legal-bar { position: absolute; left: 0; top: 2233px; width: 1200px; height: 52px; background: var(--bar); color: #d8d8d8; font-size: 13px; }
  .legal-bar p { position: absolute; left: 130px; top: 18px; }
</style>
</head>
<body>

<header class="site-header">
  <div class="brand">
    <span class="brand-mark"></span>
    <span class="brand-name">Solène Brivard</span>
  </div>
  <div class="social" aria-label="Réseaux sociaux"><span></span><span></span><span></span></div>
  <div class="lang"><span class="flag"></span>English<span class="caret"></span></div>

  <nav class="main-nav">
    <a class="current" style="left:52px">Accueil</a>
    <a style="left:162px">Agence</a>
    <a style="left:267px">Services</a>
    <a style="left:372px">Approche</a>
    <a style="left:477px">Publications</a>
    <a style="left:582px">Contact</a>
  </nav>
  <svg class="search-icon" width="16" height="16" viewBox="0 0 16 16" aria-label="Recherche">
    <circle cx="6.5" cy="6.5" r="4.5" fill="none" stroke="#e5404a" stroke-width="2"/>
    <line x1="10" y1="10" x2="14" y2="14" stroke="#e5404a" stroke-width="2.4" stroke-linecap="round"/>
  </svg>
  <div class="nav-rule"></div>
  <div class="nav-current-bar"></div>
</header>

<section class="hero">
  <div class="hero-visual" role="img" aria-label="Cube blanc marqué d'une croix rouge et ruban rouge sur fond gris clair"></div>
  <h1 class="hero-title">Cabinet-conseil en communications<br>et affaires publiques spécialisé<br>dans le <u>secteur de la santé</u></h1>
  <div class="cta">
    <span class="cta-label">En savoir plus</span>
    <span class="cta-arrow">
      <svg width="18" height="18" viewBox="0 0 18 18"><circle cx="9" cy="9" r="8" fill="none" stroke="#9a9a9a" stroke-width="1.5"/><path d="M7.5 5.5 L11 9 L7.5 12.5" fill="none" stroke="#9a9a9a" stroke-width="1.8"/></svg>
    </span>
  </div>
  <div class="slider-dots"><span class="active"></span><span></span><span></span><span></span><span></span></div>
</section>

<main>
  <div class="section-bar"></div>
  <h2 class="section-title">Publication récentes</h2>
  <div class="section-rule"></div>

  <div class="post-media" style="top:758px">
    <div class="photo" role="img" aria-label="Documents de plan de communication posés sur une table" style="background:linear-gradient(160deg,#d9dde3 0%,#b9c0cc 45%,#8a5a3c 100%)"></div>
    <div class="zoom"><svg width="14" height="14" viewBox="0 0 14 14"><circle cx="5.5" cy="5.5" r="3.8" fill="none" stroke="#fff" stroke-width="1.6"/><line x1="8.5" y1="8.5" x2="12" y2="12" stroke="#fff" stroke-width="2"/></svg></div>
  </div>
  <div class="thumbs">
    <span role="img" aria-label="Microphones" style="background:linear-gradient(#f4f4f4,#cfcfcf)"></span>
    <span role="img" aria-label="Schéma sur papier" style="background:linear-gradient(#fafafa,#dcdcdc)"></span>
    <span role="img" aria-label="Documents" style="background:linear-gradient(#e5404a,#b93039)"></span>
    <span role="img" aria-label="Table de travail" style="background:linear-gradient(#e6e6e6,#9f7a5e)"></span>
  </div>
  <article class="post-body" style="top:758px">
    <div class="bar"></div>
    <h3 class="post-title">Project Lorem Ipsum</h3>
    <div class="post-rule"></div>
    <p class="post-text">Sed ut perspiciatis unde omnis iste natus error sit voluptatem accusantium doloremque laudantium, totam rem aperiam, eaque ipsa quae ab illo inventore veritatis et quasi architecto beatae vitae dicta sunt explicabo.</p>
    <p class="post-text">Neque porro quisquam est, qui dolorem ipsum quia dolor sit amet, consectetur, adipisci velit, sed quia non numquam eius modi tempora incidunt ut labore et dolore magnam aliquam quaerat voluptatem.</p>
    <div class="post-btn">Visit Project</div>
  </article>

  <div class="post-media" style="top:1070px">
    <div class="photo" role="img" aria-label="Rangée de microphones de presse" style="background:linear-gradient(180deg,#fbfbfb 0%,#e9e9e9 55%,#bdbdbd 100%)"></div>
    <div class="zoom"><svg width="14" height="14" viewBox="0 0 14 14"><circle cx="5.5" cy="5.5" r="3.8" fill="none" stroke="#fff" stroke-width="1.6"/><line x1="8.5" y1="8.5" x2="12" y2="12" stroke="#fff" stroke-width="2"/></svg></div>
  </div>
  <article class="post-body" style="top:1070px">
    <div class="bar"></div>
    <h3 class="post-title">Project Lorem Ipsum</h3>
    <div class="post-rule"></div>
    <p class="post-text">Sed ut perspiciatis unde omnis iste natus error sit voluptatem accusantium doloremque laudantium, totam rem aperiam, eaque ipsa quae ab illo inventore veritatis et quasi architecto beatae vitae dicta sunt explicabo.</p>
    <p class="post-text">Neque porro quisquam est, qui dolorem ipsum quia dolor sit amet, consectetur, adipisci velit, sed quia non numquam eius modi tempora incidunt ut labore et dolore magnam aliquam quaerat voluptatem.</p>
    <div class="post-btn">Visit Project</div>
  </article>

  <div class="post-media" style="top:1343px">
    <div class="photo" role="img" aria-label="Pièces de verre transparent disposées en réseau" style="background:linear-gradient(135deg,#f2f2f2 0%,#cfd3d6 50%,#9ea3a8 100%)"></div>
    <div class="zoom"><svg width="14" height="14" viewBox="0 0 14 14"><circle cx="5.5" cy="5.5" r="3.8" fill="none" stroke="#fff" stroke-width="1.6"/><line x1="8.5" y1="8.5" x2="12" y2="12" stroke="#fff" stroke-width="2"/></svg></div>
  </div>
  <article class="post-body" style="top:1343px">
    <div class="bar"></div>
    <h3 class="post-title">Project Lorem Ipsum</h3>
    <div class="post-rule"></div>
    <p class="post-text">Sed ut perspiciatis unde omnis iste natus error sit voluptatem accusantium doloremque laudantium, totam rem aperiam, eaque ipsa quae ab illo inventore veritatis et quasi architecto beatae vitae dicta sunt explicabo.</p>
    <p class="post-text">Neque porro quisquam est, qui dolorem ipsum quia dolor sit amet, consectetur, adipisci velit, sed quia non numquam eius modi tempora incidunt ut labore et dolore magnam aliquam quaerat voluptatem.</p>
    <div class="post-btn">Visit Project</div>
  </article>

  <div class="post-media" style="top:1618px">
    <div class="photo" role="img" aria-label="Schéma stratégique sur papier" style="background:linear-gradient(160deg,#ffffff 0%,#ececec 60%,#d4d4d4 100%)"></div>
    <div class="zoom"><svg width="14" height="14" viewBox="0 0 14 14"><circle cx="5.5" cy="5.5" r="3.8" fill="none" stroke="#fff" stroke-width="1.6"/><line x1="8.5" y1="8.5" x2="12" y2="12" stroke="#fff" stroke-width="2"/></svg></div>
  </div>
  <article class="post-body" style="top:1618px">
    <div class="bar"></div>
    <h3 class="post-title">Project Lorem Ipsum</h3>
    <div class="post-rule"></div>
    <p class="post-text">Sed ut perspiciatis unde omnis iste natus error sit voluptatem accusantium doloremque laudantium, totam rem aperiam, eaque ipsa quae ab illo inventore veritatis et quasi architecto beatae vitae dicta sunt explicabo.</p>
    <p class="post-text">Neque porro quisquam est, qui dolorem ipsum quia dolor sit amet, consectetur, adipisci velit, sed quia non numquam eius modi tempora incidunt ut labore et dolore magnam aliquam quaerat voluptatem.</p>
    <div class="post-btn">Visit Project</div>
  </article>
</main>

<footer class="site-footer">
  <h4 class="footer-heading" style="left:130px">LATEST TWEETS</h4>
  <div class="tweets">
    <div class="tweet">Lorem ipsum dolor sit amet, Doctetuer adipiscing elit, sed diam nonummy nibh euismod<br><em>5 hours ago, via PostHive</em></div>
    <div class="tweet">Lorem ipsum dolor sit amet, Doctetuer adipiscing elit, sed diam nonummy nibh euismod<br><em>5 hours ago, via PostHive</em></div>
    <div class="tweet">Lorem ipsum dolor sit amet, Doctetuer adipiscing elit, sed diam nonummy nibh euismod<br><em>5 hours ago, via PostHive</em></div>
  </div>

  <h4 class="footer-heading" style="left:640px">LET US KNOW</h4>
  <div class="field" style="left:642px;top:75px;width:198px;height:38px">Name *</div>
  <div class="field" style="left:870px;top:75px;width:198px;height:38px">Email *</div>
  <div class="field" style="left:642px;top:120px;width:426px;height:113px">Comment:</div>
  <p class="thanks">Thank you for your comment!</p>
  <div class="send">
    <span class="send-label">Send</span>
    <span class="send-icon"><svg width="14" height="14" viewBox="0 0 14 14"><path d="M5 3 L9 7 L5 11" fill="none" stroke="#9a9a9a" stroke-width="1.8"/></svg></span>
  </div>
</footer>

<div class="legal-bar"><p>(C) Solène Brivard. Tous droits réservés.</p></div>

</body>
</html>
```